Coconut Water Packaging Appealing to Hispanic Consumers

This is a design for an aluminum can containing coconut water with pulp

Brand Name: Brisamar Coconut Water
Details:16.5fl oz (490ml)
Image: Animated man standing on a beach drinking out of a green coconut with a straw wearing sunglasses
Blurbs: "with pulp" "agua de coco con pulpa"
Background: Beach setting, sand, palm trees and ocean
Die cut attached

Target Market(s)

First and second generation Hispanic, Spanish speaking and price conscious consumers

Requirements
Must have
• Brand Name: Brisamar Coconut Water
Nice to have
• beach setting, refreshing feel

```html
<!DOCTYPE html>
<html lang="en">
<head>
<meta charset="utf-8">
<title>Brisamar Coconut Water – Can Labels</title>
<link href="https://fonts.googleapis.com/css2?family=Archivo+Narrow:wght@700&display=swap" rel="stylesheet">
<style>
  :root {
    --backdrop: #e6ecec;
    --silver-dark: #b4b8ba;
    --silver-mid: #d9dcdd;
    --silver-light: #f3f4f4;
    --rim: #9fa4a6;
    --rim-line: #8a8f91;
    --ink: #1a1a1a;
    --brand-red: #d9242b;
    --label-red: #e0301e;
    --warm-art-a: #d9a86a;
    --warm-art-b: #7fc8d6;
    --cool-art-a: #a9bde0;
    --cool-art-b: #7fb98c;
  }
  * { box-sizing: border-box; margin: 0; padding: 0; }
  html, body { width: 1200px; height: 1038px; overflow: hidden; }
  body {
    background: var(--backdrop);
    font-family: "Archivo Narrow", "Arial Narrow", sans-serif;
    color: var(--ink);
    position: relative;
  }
  .can {
    position: absolute;
    top: 162px;
    width: 365px;
    height: 686px;
  }
  .can--warm { left: 195px; }
  .can--cool { left: 650px; }
  .can-shape {
    position: absolute;
    inset: 0;
    width: 365px;
    height: 686px;
  }
  .mascot-art {
    position: absolute;
    left: 20px;
    top: 270px;
    width: 195px;
    height: 340px;
  }
  .brand-name {
    position: absolute;
    top: 118px;
    left: 22px;
    font-size: 72px;
    line-height: 1;
    letter-spacing: 1px;
    color: var(--brand-red);
    font-weight: 700;
  }
  .product-name {
    position: absolute;
    top: 196px;
    right: 28px;
    text-align: center;
    font-size: 32px;
    line-height: 0.95;
    font-weight: 700;
  }
  .blurb-en {
    position: absolute;
    top: 268px;
    right: 40px;
    font-size: 26px;
    line-height: 1;
    font-weight: 700;
  }
  .blurb-es {
    position: absolute;
    top: 300px;
    right: 18px;
    text-align: center;
    font-size: 26px;
    line-height: 1.05;
    font-weight: 700;
    color: var(--label-red);
  }
  .volume {
    position: absolute;
    top: 548px;
    right: 40px;
    text-align: center;
    font-size: 20px;
    line-height: 1.1;
    font-weight: 700;
  }
  .volume span { color: var(--label-red); display: block; }
</style>
</head>
<body>

  <section class="can can--warm">
    <svg class="can-shape" viewBox="0 0 365 686" aria-hidden="true">
      <defs>
        <linearGradient id="body-fill-warm" x1="0" y1="0" x2="1" y2="0">
          <stop offset="0" stop-color="var(--silver-dark)"/>
          <stop offset="0.3" stop-color="var(--silver-light)"/>
          <stop offset="0.65" stop-color="var(--silver-mid)"/>
          <stop offset="1" stop-color="var(--silver-dark)"/>
        </linearGradient>
      </defs>
      <rect x="36" y="0" width="293" height="18" rx="6" fill="var(--rim)"/>
      <path d="M40 18 H325 Q362 40 365 92 V596 Q362 644 322 668 H43 Q3 644 0 596 V92 Q3 40 40 18 Z" fill="url(#body-fill-warm)"/>
      <rect x="48" y="668" width="269" height="18" rx="6" fill="var(--rim)"/>
      <line x1="2" y1="92" x2="363" y2="92" stroke="var(--rim-line)" stroke-width="1" opacity="0.4"/>
      <line x1="2" y1="596" x2="363" y2="596" stroke="var(--rim-line)" stroke-width="1" opacity="0.4"/>
    </svg>
    <svg class="mascot-art" viewBox="0 0 195 340" role="img" aria-label="Cartoon man in a straw hat and sunglasses drinking from a green coconut with a straw">
      <defs>
        <linearGradient id="warm-fill" x1="0" y1="0" x2="0" y2="1">
          <stop offset="0" stop-color="var(--warm-art-a)"/>
          <stop offset="1" stop-color="var(--warm-art-b)"/>
        </linearGradient>
      </defs>
      <rect x="0" y="0" width="195" height="340" rx="24" fill="url(#warm-fill)" opacity="0.85"/>
    </svg>
    <div class="brand-name">BRISAMAR</div>
    <div class="product-name">Coconut<br>Water</div>
    <div class="blurb-en">With pulp</div>
    <div class="blurb-es">Agua de coco<br>con pulpa</div>
    <div class="volume">16.5fl oz<span>(490ml)</span></div>
  </section>

  <section class="can can--cool">
    <svg class="can-shape" viewBox="0 0 365 686" aria-hidden="true">
      <defs>
        <linearGradient id="body-fill-cool" x1="0" y1="0" x2="1" y2="0">
          <stop offset="0" stop-color="var(--silver-dark)"/>
          <stop offset="0.3" stop-color="var(--silver-light)"/>
          <stop offset="0.65" stop-color="var(--silver-mid)"/>
          <stop offset="1" stop-color="var(--silver-dark)"/>
        </linearGradient>
      </defs>
      <rect x="36" y="0" width="293" height="18" rx="6" fill="var(--rim)"/>
      <path d="M40 18 H325 Q362 40 365 92 V596 Q362 644 322 668 H43 Q3 644 0 596 V92 Q3 40 40 18 Z" fill="url(#body-fill-cool)"/>
      <rect x="48" y="668" width="269" height="18" rx="6" fill="var(--rim)"/>
      <line x1="2" y1="92" x2="363" y2="92" stroke="var(--rim-line)" stroke-width="1" opacity="0.4"/>
      <line x1="2" y1="596" x2="363" y2="596" stroke="var(--rim-line)" stroke-width="1" opacity="0.4"/>
    </svg>
    <svg class="mascot-art" viewBox="0 0 195 340" role="img" aria-label="Cartoon man in a sun hat and sunglasses, in cool blue and green tones, drinking from a green coconut with a straw">
      <defs>
        <linearGradient id="cool-fill" x1="0" y1="0" x2="0" y2="1">
          <stop offset="0" stop-color="var(--cool-art-a)"/>
          <stop offset="1" stop-color="var(--cool-art-b)"/>
        </linearGradient>
      </defs>
      <rect x="0" y="0" width="195" height="340" rx="24" fill="url(#cool-fill)" opacity="0.85"/>
    </svg>
    <div class="brand-name">BRISAMAR</div>
    <div class="product-name">Coconut<br>Water</div>
    <div class="blurb-en">With pulp</div>
    <div class="blurb-es">Agua de coco<br>con pulpa</div>
    <div class="volume">16.5fl oz<span>(490ml)</span></div>
  </section>

</body>
</html>
```